Valentines Day Helicopter Tour Mailer

The purpose behind this project is to design a mailer for helicopter tours around valentines day. Not sure exaclty all what to include as i'm not sure if i want to price on it yet but i want helicopters, hearts, and something interesting to draw attention to the service we will be offering. If we did include price it would be $169/ person. Size should be good for 8.5 by 11 paper

general public

```html
<!DOCTYPE html>
<html lang="en">
<head>
<meta charset="utf-8">
<title>Valentines Day Helicopter Tour Mailer</title>
<link href="https://fonts.googleapis.com/css2?family=Poppins:ital,wght@0,400;0,600;0,700;1,600;1,700&family=Lobster&display=swap" rel="stylesheet">
<style>
  :root {
    --backdrop: #5e5e5e;
    --ink-dark: #0b0b0b;
    --paper: #ffffff;
    --love-red: #e2121b;
    --deep-red: #8f0d12;
    --silver-light: #e6e6e6;
    --silver-dark: #6d6d6d;
    --body-text: #1b1b1b;
    --field-green: #4a5a2c;
    --blush: #e9a0aa;
  }
  html, body {
    margin: 0;
    width: 1200px;
    height: 2192px;
    overflow: hidden;
    background: var(--backdrop);
  }
  .mailer {
    position: absolute;
    left: 61px;
    top: 400px;
    width: 1078px;
    height: 1392px;
    overflow: hidden;
    background: var(--ink-dark);
    font-family: "Poppins", sans-serif;
    box-shadow: 0 30px 60px rgba(0,0,0,.45);
  }
  .photo-landscape {
    position: absolute; inset: 0;
    background: linear-gradient(180deg, #050505 0%, #0a0a0a 45%, #2c2a1c 62%, #3f4d27 78%, var(--field-green) 100%);
  }
  .photo-city {
    position: absolute; left: 380px; top: 0; width: 300px; height: 620px;
    background: linear-gradient(180deg, #1d1d1d 0%, #141414 60%, rgba(10,10,10,0) 100%);
    opacity: .8;
  }
  .photo-helicopter {
    position: absolute; left: 616px; top: 194px; width: 462px; height: 386px;
    background: radial-gradient(ellipse at 55% 70%, #7a0f12 0%, #3b0709 45%, rgba(10,10,10,0) 80%);
  }
  .waves { position: absolute; inset: 0; width: 1078px; height: 1392px; }
  .brand {
    position: absolute; left: 88px; top: 104px;
    display: flex; align-items: center; gap: 14px;
    color: var(--paper); font-weight: 600; font-size: 38px; line-height: 1;
  }
  .brand-dot { width: 22px; height: 22px; border-radius: 50%; background: var(--paper); }
  .headline { position: absolute; left: 91px; top: 258px; margin: 0; color: var(--paper); }
  .headline-big { display: block; font-weight: 700; font-size: 96px; line-height: 92px; letter-spacing: 1px; }
  .headline-sub { display: block; font-weight: 400; font-size: 46px; line-height: 58px; }
  .headline-script {
    display: block; font-family: "Lobster", cursive; color: var(--love-red);
    font-size: 96px; line-height: 100px; font-weight: 400;
  }
  .heart-photo { position: absolute; left: 58px; top: 632px; width: 520px; height: 480px; }
  .price { position: absolute; left: 186px; top: 770px; width: 200px; text-align: center; }
  .price-amount { display: block; color: var(--paper); font-weight: 600; font-size: 82px; line-height: 90px; }
  .price-unit { display: block; color: var(--love-red); font-size: 30px; line-height: 34px; }
  .tours {
    position: absolute; left: 660px; top: 644px; height: 204px;
    border-left: 3px solid var(--love-red); padding-left: 20px;
    color: var(--paper); font-size: 36px; line-height: 44px; font-weight: 400;
    padding-top: 14px; box-sizing: border-box;
  }
  .tours strong { font-weight: 600; }
  .pitch {
    position: absolute; left: 280px; top: 1108px; margin: 0;
    white-space: nowrap;
    color: var(--body-text); font-size: 18.5px; line-height: 31px;
  }
  .pitch em { color: var(--love-red); font-weight: 700; font-size: 23.5px; }
  .rule { position: absolute; left: 280px; top: 1249px; width: 618px; height: 2px; background: var(--body-text); }
  .website { position: absolute; left: 280px; top: 1280px; color: var(--body-text); font-size: 20px; }
  .phone {
    position: absolute; left: 650px; top: 1266px; display: flex; align-items: center; gap: 14px;
    color: var(--body-text); font-weight: 600; font-size: 34px; letter-spacing: 1px;
  }
  .phone svg { width: 26px; height: 26px; }
</style>
</head>
<body>
<main class="mailer">
  <div class="photo-landscape" role="img" aria-label="Aerial photo of green fields at dusk seen from a helicopter cockpit"></div>
  <div class="photo-city" role="img" aria-label="Dark city towers at night"></div>
  <div class="photo-helicopter" role="img" aria-label="Helicopter on a helipad lit in red at night"></div>

  <svg class="waves" viewBox="0 0 898 1160" preserveAspectRatio="none" aria-hidden="true">
    <defs>
      <linearGradient id="red-band" x1="0" y1="0" x2="1" y2="0">
        <stop offset="0" stop-color="#e2121b"/>
        <stop offset="1" stop-color="#8f0d12"/>
      </linearGradient>
      <linearGradient id="silver-band" x1="0" y1="0" x2="1" y2="0">
        <stop offset="0" stop-color="#8a8a8a"/>
        <stop offset=".45" stop-color="#f2f2f2"/>
        <stop offset="1" stop-color="#4a4a4a"/>
      </linearGradient>
    </defs>
    <path d="M150,1000 C260,800 520,745 898,755 L898,835 C620,805 380,830 210,960 Z" fill="url(#red-band)"/>
    <path d="M205,962 C370,830 620,805 898,835 L898,905 C640,845 400,860 250,965 Z" fill="url(#silver-band)"/>
    <path d="M80,1160 C120,1075 120,995 205,940 C380,840 640,845 898,935 L898,1160 Z" fill="url(#silver-band)"/>
    <path d="M100,1160 C140,1080 145,1000 225,948 C390,860 640,860 898,950 L898,1160 Z" fill="#ffffff"/>
  </svg>

  <div class="brand"><span class="brand-dot"></span>Skyward Helicopters</div>

  <h1 class="headline">
    <span class="headline-big">TAKE</span>
    <span class="headline-big">ROMANCE</span>
    <span class="headline-sub">to New Heights on this</span>
    <span class="headline-script">Valentines Day!</span>
  </h1>

  <svg class="heart-photo" viewBox="0 0 520 480" role="img" aria-label="Heart-shaped frame showing a pink sunset over a forest lake">
    <defs>
      <linearGradient id="heart-fill" x1="0" y1="0" x2="1" y2="1">
        <stop offset="0" stop-color="#8e2418"/>
        <stop offset=".45" stop-color="#e9a0aa"/>
        <stop offset="1" stop-color="#b5532e"/>
      </linearGradient>
    </defs>
    <path d="M260,470 C250,380 60,330 30,220 C0,110 80,20 170,40 C220,50 250,90 260,120 C275,60 330,0 410,10 C500,25 530,120 490,210 C450,300 300,330 270,420 Z" fill="url(#heart-fill)"/>
    <path d="M200,340 C130,300 60,250 60,190 C60,130 110,100 160,120 C200,135 230,160 240,200 C250,250 240,300 200,340 Z" fill="#0c0c0c" opacity=".85"/>
  </svg>

  <div class="price">
    <span class="price-amount">$169</span>
    <span class="price-unit">Per Person</span>
  </div>

  <div class="tours"><strong>HELICOPTER<br>TOURS</strong> Around<br>Great Lakes area<br>and beyond.</div>

  <p class="pitch">You will feel safe at home in our helicopters because our pilots<br>have been trained to the highest standard and we strive to be<br>the best. <em>Come enjoy the safety, security and<br>down right experience of a helicopter today!</em></p>
  <div class="rule"></div>
  <div class="website">www.skywardhelicopters.example</div>
  <div class="phone">
    <svg viewBox="0 0 24 24" aria-hidden="true"><path fill="#e2121b" d="M6.6 10.8a15.1 15.1 0 0 0 6.6 6.6l2.2-2.2a1 1 0 0 1 1-.25 11.4 11.4 0 0 0 3.6.57 1 1 0 0 1 1 1V20a1 1 0 0 1-1 1A17 17 0 0 1 3 4a1 1 0 0 1 1-1h3.5a1 1 0 0 1 1 1c0 1.25.2 2.45.57 3.57a1 1 0 0 1-.25 1z"/></svg>
    555-201-4477
  </div>
</main>
</body>
</html>
```